Business Card Design for Training Business

Clear Path Coaching is a new business that delivers training and other services with a focus on topics related to mental health and wellbeing, for example, Wellmind Response Course, Resilience etc. We have a strong focus on evidence-based psychology and neuroscience. I have a logo which I will upload with the brief, so please consider colours that work well with the logo.
Target Market(s)
Adults, workplaces (particularly government and not-for-profits)
Industry/Entity Type
Business
Contact Information for Business Card
Head Strong TrainingSamantha SellwoodDirector0438 770 850sam@headstrongtraining.com.auwww.headstrongtraining.com.au

```html
<!DOCTYPE html>
<html lang="en">
<head>
<meta charset="utf-8">
<title>Clear Path Coaching – Business Card</title>
<link href="https://fonts.googleapis.com/css2?family=Questrial&display=swap" rel="stylesheet">
<style>
  :root {
    --backdrop: #3a3a3a;
    --teal: #22b5bd;
    --teal-deep: #1ba8b0;
    --paper: #f7f7f5;
    --ring: #4a3a35;
    --ink: #4b4543;
    --ink-soft: #6b6462;
  }
  * { box-sizing: border-box; margin: 0; padding: 0; }
  html, body {
    width: 1200px;
    height: 750px;
    overflow: hidden;
    background: var(--backdrop);
    font-family: "Questrial", "Century Gothic", sans-serif;
  }
  .stage {
    position: relative;
    width: 1200px;
    height: 750px;
  }
  .card {
    position: absolute;
    left: 372px;
    width: 460px;
    height: 262px;
    border-radius: 14px;
    overflow: hidden;
  }
  .card--front { top: 106px; }
  .card--back { top: 388px; }
  .card__pattern {
    position: absolute;
    inset: 0;
    background: radial-gradient(circle at 50% 50%, var(--teal) 0%, var(--teal-deep) 100%);
  }
  .card__medallion {
    position: absolute;
    left: 113px;
    top: 14px;
    width: 234px;
    height: 234px;
    border-radius: 50%;
    background: var(--paper);
    border: 3px solid var(--ring);
    display: flex;
    flex-direction: column;
    align-items: center;
    justify-content: center;
    text-align: center;
  }
  .contact__name {
    color: var(--teal);
    font-size: 18px;
    letter-spacing: 0.2px;
    line-height: 1.1;
  }
  .contact__role {
    color: var(--ink);
    font-size: 13px;
    margin-top: 3px;
  }
  .contact__details {
    margin-top: 17px;
    color: var(--ink-soft);
    font-size: 11.5px;
    line-height: 17.5px;
  }
  .brand__dot {
    width: 50px;
    height: 50px;
    border-radius: 50%;
    background: var(--teal);
    opacity: 0.85;
  }
  .brand__name {
    margin-top: 20px;
    color: var(--ink-soft);
    font-size: 14px;
    letter-spacing: 2px;
    text-transform: uppercase;
  }
</style>
</head>
<body>
<main class="stage">
  <section class="card card--front">
    <div class="card__pattern" role="img" aria-label="Teal background with an interlaced white line pattern"></div>
    <div class="card__medallion">
      <p class="contact__name">Rebecca Tanfield</p>
      <p class="contact__role">Director</p>
      <p class="contact__details">
        0491 362 517<br>
        bec@clearpathcoaching.example.au<br>
        www.clearpathcoaching.example.au
      </p>
    </div>
  </section>

  <section class="card card--back">
    <div class="card__pattern" role="img" aria-label="Teal background with an interlaced white line pattern"></div>
    <div class="card__medallion">
      <div class="brand__dot"></div>
      <p class="brand__name">Clear Path Coaching</p>
    </div>
  </section>
</main>
</body>
</html>
```